Business Card Design For Office Furniture Clearance Company

Kestrel Office Clearance - our company name pretty much explains what we do, we clear offices for high end clients, mainly plc's and large international companies.

We require a nice looking business card that displays professionalism but without being too serious.

It would be nice to see just a little more than a conventional boring business card, make sure you add some flare.

Industry/Entity Type

Office Furniture

Contact Information for Business Card

CARD 1

Mark Holloway
Director
mark@kestrelofficeclearance.co.uk
m: 07700 153928

t: 01632 960418
www.kestrelofficeclearance.co.uk

Kestrel Office Clearance
Unit K4 B
2-8 Fenwick Lane
Ashcombe
Northbridge
ZZ9 4QT

free office clearances… you cant get better than that.

CARD 2

Peter Radford
Director
peter@kestrelofficeclearance.co.uk
m: 07700 382615

t: 01632 960418

Kestrel Office Clearance
Unit K4 B
2-8 Fenwick Lane
Ashcombe
Northbridge
ZZ9 4QT

Font styles to use
Sans Serif

Requirements
Must have
• A white background - as we have a blue logo.
Nice to have
• Nice use of the logo - play around with this and dissect it.

```html
<!DOCTYPE html>
<html lang="en">
<head>
<meta charset="utf-8">
<title>Kestrel Office Clearance – Business Cards</title>
<link rel="stylesheet" href="https://fonts.googleapis.com/css2?family=Quicksand:wght@500;600;700&display=swap">
<style>
  :root {
    --stage: #2a2a2a;
    --card-black: #050505;
    --white: #ffffff;
    --blue: #1a7fc1;
    --blue-deep: #1d5f95;
  }
  * { box-sizing: border-box; margin: 0; padding: 0; }
  html, body {
    width: 1200px; height: 900px; overflow: hidden;
    background: var(--stage);
    font-family: "Quicksand", "Helvetica Neue", Arial, sans-serif;
  }
  .stage { position: relative; width: 1200px; height: 900px; }

  .card {
    position: absolute;
    width: 700px; height: 400px;
    border-radius: 26px;
    background: var(--card-black);
    overflow: hidden;
    box-shadow: 0 18px 40px rgba(0,0,0,.55);
  }

  /* Front */
  .card-front { left: 110px; top: 50px; }
  .flame-motif {
    position: absolute; left: 40px; top: 60px;
    width: 230px; height: 330px;
    background: radial-gradient(ellipse at 50% 55%, #333 0%, #222 55%, rgba(5,5,5,0) 75%);
    border-radius: 50% 50% 40% 60%;
  }
  .front-brand {
    position: absolute; left: 0; right: 0; top: 70px;
    text-align: center; color: var(--white);
  }
  .brand-dot {
    width: 120px; height: 120px; border-radius: 50%;
    background: var(--white); margin: 0 auto 22px;
  }
  .brand-name {
    font-weight: 700; font-size: 24px; letter-spacing: .5px;
    text-transform: uppercase;
  }
  .tagline {
    margin-top: 14px;
    font-weight: 600; font-size: 20px; text-transform: uppercase;
  }
  .front-web {
    position: absolute; right: 34px; bottom: 30px;
    color: var(--white); font-weight: 600; font-size: 15px; letter-spacing: .5px;
  }

  /* Back */
  .card-back { left: 410px; top: 480px; }
  .card-back svg.panel { position: absolute; inset: 0; }
  .back-brand {
    position: absolute; left: 0; top: 250px; width: 400px;
    text-align: center; color: var(--blue-deep);
    font-weight: 700; font-size: 46px;
  }
  .contact {
    position: absolute; right: 30px; top: 40px;
    text-align: right; color: var(--white);
    font-weight: 600; font-size: 14px; line-height: 1.35;
  }
  .contact-name {
    color: var(--blue); font-size: 27px; font-weight: 600;
    text-transform: uppercase; line-height: 1.1;
  }
  .contact-role { font-size: 13px; text-transform: uppercase; margin-bottom: 10px; }
  .contact-address { margin-bottom: 12px; }
  .contact-line { display: flex; justify-content: flex-end; align-items: center; gap: 10px; }
  .contact-line svg { width: 13px; height: 13px; flex: none; }
</style>
</head>
<body>
<main class="stage">

  <section class="card card-front">
    <div class="flame-motif" role="img" aria-label="Faint grey flame-like decorative motif"></div>
    <div class="front-brand">
      <div class="brand-dot"></div>
      <p class="brand-name">Kestrel Office Clearance</p>
      <p class="tagline">Free office clearances… you cant get better than that</p>
    </div>
    <p class="front-web">www.kestrelofficeclearance.co.uk</p>
  </section>

  <section class="card card-back">
    <svg class="panel" viewBox="0 0 700 400" aria-hidden="true">
      <circle cx="60" cy="300" r="330" fill="#ffffff"/>
    </svg>
    <p class="back-brand">Kestrel</p>

    <div class="contact">
      <p class="contact-name">Mark Holloway</p>
      <p class="contact-role">Director</p>
      <p class="contact-address">Unit K4 B, 2-8 Fenwick Lane,<br>Ashcombe,<br>Northbridge, ZZ9 4QT</p>
      <p class="contact-line">07700 153928
        <svg viewBox="0 0 12 12"><rect x="3" y="1" width="6" height="10" rx="1" fill="none" stroke="#1a7fc1" stroke-width="1.2"/></svg></p>
      <p class="contact-line">01632 960418
        <svg viewBox="0 0 12 12"><path d="M2 2 L4.5 1.5 L5.5 4 L4 5 Q5 7.5 7 8 L8 6.5 L10.5 7.5 L10 10 Q4 10 2 2 Z" fill="#1a7fc1"/></svg></p>
      <p class="contact-line">mark@kestrelofficeclearance.co.uk
        <svg viewBox="0 0 12 12"><rect x="1" y="2.5" width="10" height="7" fill="none" stroke="#1a7fc1" stroke-width="1.2"/><path d="M1 2.5 L6 6.5 L11 2.5" fill="none" stroke="#1a7fc1" stroke-width="1.2"/></svg></p>
      <p class="contact-line">www.kestrelofficeclearance.co.uk
        <svg viewBox="0 0 12 12"><circle cx="6" cy="6" r="4.8" fill="none" stroke="#1a7fc1" stroke-width="1.2"/><path d="M1.2 6 H10.8 M6 1.2 Q3 6 6 10.8 M6 1.2 Q9 6 6 10.8" fill="none" stroke="#1a7fc1" stroke-width="1"/></svg></p>
    </div>
  </section>

</main>
</body>
</html>
```